Looking to Redesign Brevonix.com website

You guys did one of the brochures for brevonix.com and I would like to see if we can go ahead and get an estimate for a redesigned web site for the company. We currently have a couple of pages on brevonix.com which are very much a starter type site.

The new design will need to reflect some of the things discussed in the brochure. It will have flash. Needs to be designed for simple hosting using cpanels.

The site needs to have between 12 and 15 pages with flash pages to move through features. Integrated with twitter like it is now, and contact forms delivered from our CRM along with other interactive features such as subscription to newsletter, etc...

I don't have lots of details on how to proceed yet, but here are some competitor sites:

Can we take a look at potential costs involved in the redo of the site as vague as my description above can permit.

Target Market(s)

Business to Business

Number of Pages Required

5+ page

Font styles to use
Sans Serif

Requirements
Must have
• Must have professional feel. Similar to brochure. and logo.
• Include our story in the discussion.
• embedded links to our CRM for popup contact forms.
• Logo files and 2 types of brochures uploaded.
• Important to keep color scheme
Nice to have
• Flash and some movement
Should not have
• Not sure yet

```html
<!DOCTYPE html>
<html lang="en">
<head>
<meta charset="utf-8">
<title>Brevonix Univesal Communications</title>
<link href="https://fonts.googleapis.com/css2?family=Raleway:wght@400;500;600&family=Open+Sans:wght@400;600&display=swap" rel="stylesheet">
<style>
  :root {
    --red: #c8161d;
    --red-dark: #a81218;
    --ink: #222222;
    --text: #555555;
    --muted: #888888;
    --icon-grey: #4a4a4a;
    --light: #f2f2f3;
    --white: #ffffff;
    --footer: #2b2b2b;
    --line: #d9d9d9;
  }
  * { margin: 0; padding: 0; box-sizing: border-box; }
  html, body { width: 1200px; height: 2476px; overflow: hidden; }
  body { position: relative; background: var(--white); font-family: "Open Sans", Arial, sans-serif; color: var(--text); }
  .section { position: absolute; left: 0; width: 1200px; }
  .heading { font-family: "Raleway", Arial, sans-serif; font-weight: 500; }

  /* header */
  .site-header { top: 0; height: 102px; background: var(--white); }
  .brand { position: absolute; left: 180px; top: 26px; display: flex; align-items: center; gap: 12px; }
  .brand-dot { width: 46px; height: 46px; border-radius: 50%; background: var(--red); }
  .brand-name { font-family: "Raleway", Arial, sans-serif; font-weight: 600; font-size: 26px; color: var(--red); }
  .main-nav { position: absolute; right: 183px; top: 0; height: 102px; display: flex; gap: 32px; }
  .main-nav a { font-family: "Raleway", Arial, sans-serif; font-size: 14px; color: var(--ink); text-decoration: none; line-height: 108px; position: relative; }
  .main-nav a.active { color: var(--red); }
  .main-nav a.active::after { content: ""; position: absolute; left: -6px; right: -6px; bottom: 0; height: 3px; background: var(--red); }

  /* hero */
  .hero { top: 102px; height: 482px; }
  .hero-photo { position: absolute; inset: 0; background: linear-gradient(100deg, #5f7d98 0%, #9fb6ca 40%, #c9d4dc 62%, #7d8ea0 100%); }
  .hero-copy { position: absolute; left: 173px; top: 146px; color: var(--white); }
  .hero-kicker { font-family: "Raleway", Arial, sans-serif; font-size: 26px; letter-spacing: 0.5px; }
  .hero-title { font-family: "Raleway", Arial, sans-serif; font-size: 46px; letter-spacing: 1px; line-height: 1.1; margin-top: 4px; }
  .hero-text { font-size: 13px; line-height: 22px; width: 430px; margin-top: 10px; }
  .hero-dots { display: flex; gap: 6px; margin-top: 16px; }
  .hero-dots span { width: 15px; height: 15px; border-radius: 50%; background: var(--white); }
  .hero-dots span.current { background: transparent; border: 2px solid var(--white); }

  /* about */
  .about { top: 584px; height: 366px; background: linear-gradient(160deg, #f7f7f8 0%, #ececee 50%, #f5f5f6 100%); text-align: center; }
  .about h2 { font-size: 28px; color: var(--ink); margin-top: 54px; }
  .about p { width: 640px; margin: 22px auto 0; font-size: 11.5px; line-height: 23px; color: var(--text); }
  .service-icons { position: absolute; top: 200px; left: 239px; display: flex; gap: 24px; }
  .service-icons svg { width: 100px; height: 100px; }

  /* why */
  .why { top: 950px; height: 390px; background: radial-gradient(ellipse at 40% 40%, #cf262c 0%, var(--red) 55%, var(--red-dark) 100%); color: var(--white); }
  .why-copy { position: absolute; left: 180px; top: 78px; width: 410px; }
  .why h2 { font-size: 28px; font-weight: 400; letter-spacing: 0.5px; }
  .why p { font-size: 11.5px; line-height: 19px; margin-top: 12px; }
  .why p + p { margin-top: 8px; }
  .btn-outline { display: inline-block; margin-top: 20px; padding: 8px 17px; border: 1.5px solid var(--white); font-family: "Raleway", Arial, sans-serif; font-size: 11px; color: var(--white); text-decoration: none; }
  .tablet { position: absolute; left: 632px; top: 73px; width: 386px; height: 215px; background: var(--white); border: 2px solid #cfcfcf; border-radius: 16px; box-shadow: 0 4px 12px rgba(0,0,0,0.25); }
  .tablet-screen { position: absolute; left: 32px; top: 10px; right: 14px; bottom: 10px; background: linear-gradient(135deg, #eeeeea, #dedbd2); border: 1px solid #999; }
  .tablet-button { position: absolute; left: 9px; top: 100px; width: 14px; height: 14px; border-radius: 50%; border: 1px solid #999; }

  /* benefits */
  .benefits { top: 1340px; height: 404px; background: var(--white); text-align: center; }
  .benefits h2 { font-size: 22px; color: var(--ink); margin-top: 57px; }
  .benefit-grid { position: absolute; left: 177px; top: 112px; display: grid; grid-template-columns: repeat(3, 289px); row-gap: 42px; text-align: left; }
  .benefit { display: flex; gap: 12px; }
  .benefit-icon { flex: none; width: 66px; height: 66px; border-radius: 50%; border: 1px solid var(--line); display: flex; align-items: center; justify-content: center; }
  .benefit-icon svg { width: 34px; height: 34px; }
  .benefit h3 { font-family: "Raleway", Arial, sans-serif; font-weight: 400; font-size: 17px; color: var(--red); margin-top: 2px; }
  .benefit p { font-size: 9.5px; line-height: 14px; color: var(--muted); width: 190px; margin-top: 4px; }
  .btn-pill { position: absolute; left: 529px; top: 330px; width: 136px; height: 34px; border: 1.5px solid #999; border-radius: 17px; font-family: "Raleway", Arial, sans-serif; font-size: 12px; color: var(--ink); line-height: 31px; text-align: center; text-decoration: none; }

  /* features */
  .features { top: 1744px; height: 360px; border-top: 1px solid #e6e6e6; }
  .features-photo { position: absolute; left: 0; top: 0; width: 599px; height: 360px; background: linear-gradient(120deg, #8a8f86 0%, #5b6150 45%, #3d4234 75%, #6e7368 100%); }
  .features-copy { position: absolute; left: 644px; top: 52px; width: 420px; }
  .features h2 { font-size: 25px; color: var(--red); font-weight: 400; }
  .feature-list { list-style: none; margin-top: 20px; }
  .feature-list li { position: relative; padding-left: 22px; font-size: 11.5px; line-height: 19px; color: var(--text); margin-bottom: 10px; }
  .feature-list li::before { content: ""; position: absolute; left: 2px; top: 6px; width: 6px; height: 6px; border-right: 1.5px solid #777; border-top: 1.5px solid #777; transform: rotate(45deg); }

  /* newsletter */
  .newsletter { top: 2104px; height: 247px; background: linear-gradient(100deg, #2c2a27 0%, #4a4640 45%, #3a3733 70%, #25231f 100%); text-align: center; color: var(--white); }
  .newsletter h2 { font-size: 26px; font-weight: 500; margin-top: 48px; letter-spacing: 0.5px; }
  .newsletter p { font-size: 13.5px; margin-top: 4px; }
  .subscribe-form { position: absolute; left: 366px; top: 135px; width: 482px; height: 41px; background: var(--white); border: 2px solid var(--white); display: flex; }
  .subscribe-form .field { flex: 1; display: flex; align-items: center; gap: 10px; padding-left: 10px; font-size: 12.5px; color: var(--muted); text-align: left; }
  .subscribe-form .field svg { width: 18px; height: 14px; }
  .subscribe-form .submit { width: 122px; background: var(--red); color: var(--white); font-family: "Raleway", Arial, sans-serif; font-size: 13px; line-height: 37px; }

  /* footer */
  .site-footer { top: 2351px; height: 125px; background: var(--footer); color: var(--white); }
  .footer-nav { position: absolute; left: 177px; top: 36px; display: flex; gap: 27px; }
  .footer-nav a { font-family: "Raleway", Arial, sans-serif; font-size: 14px; color: var(--white); text-decoration: none; }
  .copyright { position: absolute; left: 177px; top: 68px; font-size: 11px; color: #cccccc; }
  .social { position: absolute; left: 884px; top: 32px; display: flex; gap: 5px; }
  .social span { width: 32px; height: 32px; border-radius: 50%; border: 1.5px solid var(--white); }
</style>
</head>
<body>

<header class="section site-header">
  <div class="brand"><span class="brand-dot"></span><span class="brand-name">Brevonix</span></div>
  <nav class="main-nav">
    <a href="#" class="active">HOME</a><a href="#">ABOUT</a><a href="#">WHY US</a><a href="#">FEATURES</a><a href="#">ADVANTAGES</a><a href="#">SUPPORT</a>
  </nav>
</header>

<section class="section hero">
  <div class="hero-photo" role="img" aria-label="Business team reviewing a tablet with network connection graphics"></div>
  <div class="hero-copy">
    <div class="hero-kicker">BREVONIX UNIVESAL</div>
    <h1 class="hero-title">COMMUNICATIONS</h1>
    <p class="hero-text">Aorem ipsum dolor sit amet consectetuer adipiscing elit Nam cursus Morbi ut mi Nullam enim leo egestas id condimentum</p>
    <div class="hero-dots"><span class="current"></span><span></span><span></span><span></span></div>
  </div>
</section>

<section class="section about">
  <h2 class="heading">ABOUT OUR COMPANY</h2>
  <p>Brevonix Universal Communication was born out of the desire to offer reliable, affordable phone systems for the small- to medium-sized business. Since 2003, we have offered hosted VOIP PBX and call routing services, but they were bundled with larger IT services. As such, it was only cost-effective for the large corporate client.</p>
  <div class="service-icons">
    <svg viewBox="0 0 100 100" aria-label="Feed"><circle cx="50" cy="50" r="48" fill="var(--icon-grey)"/><circle cx="36" cy="64" r="5" fill="#fff"/><path d="M31 46a23 23 0 0 1 23 23M31 33a36 36 0 0 1 36 36" stroke="#fff" stroke-width="6" fill="none"/></svg>
    <svg viewBox="0 0 100 100" aria-label="Email"><circle cx="50" cy="50" r="48" fill="var(--icon-grey)"/><rect x="28" y="34" width="44" height="32" fill="#fff"/><path d="M28 34l22 18 22-18" stroke="var(--icon-grey)" stroke-width="3" fill="none"/></svg>
    <svg viewBox="0 0 100 100" aria-label="Chat"><circle cx="50" cy="50" r="48" fill="var(--icon-grey)"/><ellipse cx="50" cy="47" rx="24" ry="17" fill="#fff"/><path d="M36 58l-6 12 16-8z" fill="#fff"/><circle cx="40" cy="47" r="3" fill="var(--icon-grey)"/><circle cx="50" cy="47" r="3" fill="var(--icon-grey)"/><circle cx="60" cy="47" r="3" fill="var(--icon-grey)"/></svg>
    <svg viewBox="0 0 100 100" aria-label="Web"><circle cx="50" cy="50" r="48" fill="var(--icon-grey)"/><circle cx="50" cy="50" r="21" fill="none" stroke="#fff" stroke-width="4"/><path d="M29 50h42M50 29c-10 12-10 30 0 42M50 29c10 12 10 30 0 42" stroke="#fff" stroke-width="3" fill="none"/></svg>
    <svg viewBox="0 0 100 100" aria-label="Fax"><circle cx="50" cy="50" r="48" fill="var(--icon-grey)"/><rect x="37" y="28" width="26" height="12" fill="#fff"/><rect x="27" y="42" width="46" height="20" rx="3" fill="#fff"/><rect x="36" y="56" width="28" height="16" fill="#fff" stroke="var(--icon-grey)" stroke-width="2"/></svg>
    <svg viewBox="0 0 100 100" aria-label="Mobile"><circle cx="50" cy="50" r="48" fill="var(--icon-grey)"/><rect x="38" y="26" width="24" height="46" rx="4" fill="none" stroke="#fff" stroke-width="4"/><circle cx="50" cy="65" r="2.5" fill="#fff"/></svg>
  </div>
</section>

<section class="section why">
  <div class="why-copy">
    <h2 class="heading">WHY BREVONIX</h2>
    <p>Honestly, your office phone system is probably the least sexy thing in your company – the minute the system is down, you’re out of business – so you need a phone system that you can count on every minute of every day.</p>
    <p>But your phone system doesn’t have to be boring, it can look great, too! With a sleek design and customized logos, these phones add a distinctive look sitting on the desk. What is even better, is how good this system makes you look to your customers. Whatever image you want to portray.</p>
    <a href="#" class="btn-outline">LEARN MORE</a>
  </div>
  <div class="tablet">
    <span class="tablet-button"></span>
    <div class="tablet-screen" role="img" aria-label="Unified communication network diagram linking client offices to redundant telephony providers"></div>
  </div>
</section>

<section class="section benefits">
  <h2 class="heading">OUR BENEFITS</h2>
  <div class="benefit-grid">
    <div class="benefit"><div class="benefit-icon"><svg viewBox="0 0 34 34"><path d="M27 6c-8 0-14 5-16 12l5 5c7-2 12-8 11-17zM11 18l-5 1 3 3M16 23l-1 5-3-3M9 25l-3 3" stroke="var(--red)" stroke-width="2" fill="var(--red)"/></svg></div><div><h3>Quick ROI</h3><p>Lorem ipsum dolor sit amet consectetuer adipiscing elit Nam cursus Morbi ut mi Nullam enim leo egestas</p></div></div>
    <div class="benefit"><div class="benefit-icon"><svg viewBox="0 0 34 34"><path d="M17 4l11 4v8c0 7-5 12-11 14C11 28 6 23 6 16V8z" fill="none" stroke="var(--red)" stroke-width="2.5"/><path d="M12 17l4 4 7-8" fill="none" stroke="var(--red)" stroke-width="2.5"/></svg></div><div><h3>Secure</h3><p>Lorem ipsum dolor sit amet consectetuer adipiscing elit Nam cursus Morbi ut mi Nullam enim leo egestas</p></div></div>
    <div class="benefit"><div class="benefit-icon"><svg viewBox="0 0 34 34"><rect x="5" y="7" width="24" height="16" fill="none" stroke="var(--red)" stroke-width="2.5"/><path d="M2 27h30M10 19l4-5 4 3 5-6" fill="none" stroke="var(--red)" stroke-width="2"/></svg></div><div><h3>Easy Installation</h3><p>Lorem ipsum dolor sit amet consectetuer adipiscing elit Nam cursus Morbi ut mi Nullam enim leo egestas</p></div></div>
    <div class="benefit"><div class="benefit-icon"><svg viewBox="0 0 34 34"><rect x="5" y="19" width="10" height="10" fill="none" stroke="var(--red)" stroke-width="2.5"/><path d="M5 13V5h8M21 5h8v8M29 21v8h-8M15 19l12-12M20 7h7v7" fill="none" stroke="var(--red)" stroke-width="2.5" stroke-dasharray="3 2"/></svg></div><div><h3>Expandable</h3><p>Lorem ipsum dolor sit amet consectetuer adipiscing elit Nam cursus Morbi ut mi Nullam enim leo egestas</p></div></div>
    <div class="benefit"><div class="benefit-icon"><svg viewBox="0 0 34 34"><circle cx="10" cy="21" r="6" fill="none" stroke="var(--red)" stroke-width="2.5"/><circle cx="24" cy="21" r="6" fill="none" stroke="var(--red)" stroke-width="2.5"/><path d="M16 21h2M4 20L7 8M30 20L27 8" stroke="var(--red)" stroke-width="2.5" fill="none"/></svg></div><div><h3>Intuitive</h3><p>Lorem ipsum dolor sit amet consectetuer adipiscing elit Nam cursus Morbi ut mi Nullam enim leo egestas</p></div></div>
    <div class="benefit"><div class="benefit-icon"><svg viewBox="0 0 34 34"><circle cx="17" cy="17" r="8" fill="none" stroke="var(--red)" stroke-width="3"/><path d="M17 3v5M17 26v5M3 17h5M26 17h5M7 7l4 4M23 23l4 4M27 7l-4 4M7 27l4-4" stroke="var(--red)" stroke-width="3"/></svg></div><div><h3>Customized</h3><p>Lorem ipsum dolor sit amet consectetuer adipiscing elit Nam cursus Morbi ut mi Nullam enim leo egestas</p></div></div>
  </div>
  <a href="#" class="btn-pill">VIEW ALL</a>
</section>

<section class="section features">
  <div class="features-photo" role="img" aria-label="Young woman outdoors in a city using a tablet"></div>
  <div class="features-copy">
    <h2 class="heading">OUR FEATURES</h2>
    <ul class="feature-list">
      <li>Integrated Phone services for one desk to 100 and beyond</li>
      <li>Work whereever you or your employees are form home, the office, the beach! Brevonix follow you</li>
      <li>Flexible system designed for the unique needs of your company</li>
      <li>Connect multiple location into one system</li>
      <li>Easy to add one station at a time as your bussiness grows</li>
      <li>Expand employee options by setting up work at home stations</li>
    </ul>
  </div>
</section>

<section class="section newsletter" role="img" aria-label="Dark background of hands typing on a keyboard">
  <h2 class="heading">NEWSLETTER SUBSCRIBE</h2>
  <p>Lorem ipsum dolor sit amet consectetuer adipiscing elit Nam cursus Morbi ut mi Nullam enim</p>
  <div class="subscribe-form">
    <div class="field"><svg viewBox="0 0 18 14"><rect width="18" height="14" fill="#bbb"/><path d="M0 0l9 7 9-7" stroke="#fff" stroke-width="1.5" fill="none"/></svg>Email address</div>
    <div class="submit">SUBSCRIBE</div>
  </div>
</section>

<footer class="section site-footer">
  <nav class="footer-nav"><a href="#">HOME</a><a href="#">ABOUT</a><a href="#">WHY US</a><a href="#">FEATURES</a><a href="#">ADVANTAGES</a><a href="#">SUPPORT</a></nav>
  <div class="copyright">© 2016 Company Name &nbsp;All right reserved &nbsp;Term of Use</div>
  <div class="social"><span></span><span></span><span></span><span></span></div>
</footer>

</body>
</html>
```